Car transport business

We need a new business card design. Attached is our old card sample. I would just like to adjust the logo colors (blue and red) to be brighter. I changed my name to the brighter red and the word dispatcher to a brighter blue as an example. But you can adjust those colors further. And then perhaps you can use the same colors for the card design but use your imagination.

As a suggestion so the card stands out I would like to add a clip art of car carrier truck. Attached are examples of that as well

```html
<!DOCTYPE html>
<html lang="en">
<head>
<meta charset="utf-8">
<title>Swift Haul – Business Card</title>
<link rel="stylesheet" href="https://fonts.googleapis.com/css2?family=Arimo:wght@400;700&display=swap">
<style>
  :root {
    --bg: #b9b9b9;
    --brand-red: #ed1c24;
    --brand-blue: #1b75bc;
    --gradient-mid: #6e4f86;
    --card-white: #ffffff;
    --ghost: #f1f1f1;
    --shadow: rgba(0, 0, 0, 0.45);
  }
  * { margin: 0; padding: 0; box-sizing: border-box; }
  html, body {
    width: 1200px; height: 900px; overflow: hidden;
    background: var(--bg);
    font-family: "Arimo", Arial, sans-serif;
  }
  .stage { position: relative; width: 1200px; height: 900px; }
  .card {
    position: absolute;
    width: 560px; height: 320px;
    border-radius: 26px;
    box-shadow: 0 6px 10px var(--shadow);
    overflow: hidden;
  }
  .card--front {
    left: 80px; top: 110px;
    background: linear-gradient(35deg, var(--brand-blue) 0%, var(--gradient-mid) 50%, var(--brand-red) 100%);
  }
  .card--front .brand-ghost {
    position: absolute; right: 70px; top: -40px;
    width: 260px; height: 400px;
    border-radius: 50%;
    background: rgba(255, 255, 255, 0.05);
  }
  .brand {
    position: absolute;
    display: flex; align-items: center; gap: 14px;
    font-weight: 700; text-transform: uppercase;
    letter-spacing: 3px; white-space: nowrap;
  }
  .brand__dot { width: 26px; height: 26px; border-radius: 50%; }
  .card--front .brand { left: 130px; top: 138px; font-size: 40px; color: var(--card-white); }
  .card--front .brand__dot { background: var(--card-white); }

  .card--back { left: 560px; top: 470px; background: var(--card-white); }
  .card--back .brand-ghost {
    position: absolute; right: -40px; top: -30px;
    width: 300px; height: 420px; border-radius: 50%;
    border: 26px solid var(--ghost);
  }
  .card--back .brand { left: 40px; top: 60px; font-size: 36px; color: var(--brand-blue); }
  .card--back .brand__dot { background: var(--brand-red); }

  .person { position: absolute; left: 70px; top: 150px; }
  .person__name { font-size: 30px; font-weight: 400; text-transform: uppercase; letter-spacing: 1px; }
  .person__first { color: var(--brand-blue); }
  .person__last { color: var(--brand-red); }
  .person__title { font-size: 17px; color: var(--brand-blue); text-transform: uppercase; letter-spacing: 1px; margin-top: 2px; }

  .contact { position: absolute; left: 70px; top: 228px; list-style: none; }
  .contact__item { display: flex; align-items: center; gap: 12px; font-size: 19px; color: var(--brand-red); line-height: 26px; }
  .contact__icon { width: 18px; height: 18px; fill: var(--brand-blue); flex: none; }
</style>
</head>
<body>
<main class="stage">
  <section class="card card--front" aria-label="Card front">
    <div class="brand-ghost"></div>
    <div class="brand"><span class="brand__dot"></span>Swift Haul</div>
  </section>

  <section class="card card--back" aria-label="Card back">
    <div class="brand-ghost"></div>
    <div class="brand"><span class="brand__dot"></span>Swift Haul</div>

    <div class="person">
      <p class="person__name"><span class="person__first">Dan</span> <span class="person__last">Morrow</span></p>
      <p class="person__title">Diapatcher</p>
    </div>

    <ul class="contact">
      <li class="contact__item">
        <svg class="contact__icon" viewBox="0 0 24 24" aria-hidden="true"><path d="M6.6 10.8a15 15 0 0 0 6.6 6.6l2.2-2.2a1 1 0 0 1 1-.25 11.4 11.4 0 0 0 3.6.57 1 1 0 0 1 1 1V20a1 1 0 0 1-1 1A17 17 0 0 1 3 4a1 1 0 0 1 1-1h3.5a1 1 0 0 1 1 1c0 1.25.2 2.45.57 3.57a1 1 0 0 1-.25 1z"/></svg>
        555-014-2210
      </li>
      <li class="contact__item">
        <svg class="contact__icon" viewBox="0 0 24 24" aria-hidden="true"><path d="M6 2h12v6H6zM3 9h18a2 2 0 0 1 2 2v6h-4v5H5v-5H1v-6a2 2 0 0 1 2-2zm4 8v3h10v-3z"/></svg>
        555-014-2288
      </li>
      <li class="contact__item">
        <svg class="contact__icon" viewBox="0 0 24 24" aria-hidden="true"><path d="M2 5h20v14H2zm2 2v.5l8 5 8-5V7l-8 5z"/></svg>
        swifthaulinc@example.com
      </li>
    </ul>
  </section>
</main>
</body>
</html>
```